website re-design - the brickleaf studio

The Brickleaf Studio is an existing website that we built using a new zealand based online CMS tool which is quite flexible and accomodates custom designs. You can check it here: http://www.pagecrafter.example.nz/.

We have a logo already and the content on the website is OK.
The website can be found at www.thebrickleafstudio.example.au

mainly the homepage, but if the design is easily adapted to the other pages then, we will commission the winner to update these pages also.
Updates

Hi there,  I am uploading an image to be used as the main image on the homepage design,  so all submissions have the same image.

Target Market(s)

property developers, architects, builders, home buyers

Industry/Entity Type

Shop

Requirements
Must have
• Must utilise the existing CMS or at least be compatible to upload
Nice to have
• a promotional banner that can be turned off and on and changed as required as we offer different promotions over time.

```html
<!DOCTYPE html>
<html lang="en">
<head>
<meta charset="utf-8">
<title>About Us – The Brickleaf Studio</title>
<link href="https://fonts.googleapis.com/css2?family=Arimo:wght@400;700&family=Open+Sans:wght@300;400;600&display=swap" rel="stylesheet">
<style>
:root{
  --ink:#1c1c1c;
  --side:#2b2b2b;
  --side-2:#333;
  --orange:#f39019;
  --page:#e6e6e6;
  --card:#ffffff;
  --text:#555;
  --muted:#999;
  --blue:#2a6ebd;
}
*{box-sizing:border-box;margin:0;padding:0}
html,body{width:1200px;height:3224px;overflow:hidden}
body{position:relative;background:var(--page);font-family:Arimo,Arial,sans-serif;color:var(--text)}
.sidebar{position:absolute;left:0;top:0;width:400px;height:3100px;background:linear-gradient(90deg,#262626,var(--side-2))}
.masthead{position:absolute;left:400px;top:0;width:800px;height:232px;background:var(--ink);border-bottom:4px solid #111}
.brand{position:absolute;left:30px;top:50px;display:flex;align-items:center;gap:16px}
.brand-mark{width:62px;height:62px;border:3px solid var(--orange)}
.brand-name{font-family:"Open Sans",sans-serif;font-weight:400;font-size:34px;color:#fff;text-transform:uppercase;letter-spacing:1px;line-height:1}
.brand-tag{font-family:"Open Sans",sans-serif;font-size:17px;color:var(--orange);letter-spacing:1px;margin-top:6px;text-transform:uppercase}
.nav{position:absolute;left:20px;top:190px;display:flex;gap:4px}
.nav a{font-size:13px;color:#ddd;text-decoration:none;padding:8px 10px}
.nav a.active{background:var(--orange);color:#fff}
.side-tab{position:absolute;left:0;top:180px;width:340px;height:40px;background:var(--orange);color:#111;font-weight:700;font-size:17px;padding:10px 0 0 80px;text-transform:uppercase}
.search{position:absolute;left:85px;top:262px;width:280px;height:28px;display:flex}
.search span{flex:1;background:#444;border:1px solid #555;color:#888;font-size:12px;padding:6px 8px}
.search i{width:28px;background:var(--orange)}
.intro{position:absolute;left:70px;top:340px;width:300px;text-align:right;font-family:"Open Sans",sans-serif;font-weight:300;font-size:24px;line-height:33px;color:#b5b5b5}
.promo{position:absolute;background:linear-gradient(#2f7fd1,#174f95);border-radius:4px}
.promo.one{left:95px;top:712px;width:155px;height:120px}
.promo.two{left:95px;top:880px;width:155px;height:170px}
.side-h{position:absolute;right:30px;font-family:"Open Sans",sans-serif;font-size:22px;color:var(--orange);text-transform:uppercase;text-align:right}
.side-rule{position:absolute;left:60px;width:310px;border-top:1px solid #555}
.field{position:absolute;left:85px;width:280px;height:28px;background:#444;border:1px solid #555;color:#888;font-size:12px;padding:7px 8px}
.subscribe{position:absolute;left:85px;top:1265px;width:120px;height:30px;background:var(--blue);color:#fff;font-size:12px;font-weight:700;text-align:center;padding-top:8px;text-transform:uppercase}
.map{position:absolute;left:60px;top:1430px;width:310px;height:150px;background:linear-gradient(135deg,#dfe3d6,#c8d4e0)}
.address{position:absolute;right:30px;top:1610px;text-align:right;font-size:12px;line-height:18px;color:#aaa}
.address b{color:var(--orange);font-weight:400}
.card{position:absolute;left:415px;top:252px;width:770px;height:2830px;background:var(--card);padding:30px 40px;overflow:hidden}
.page-title{font-family:"Open Sans",sans-serif;font-weight:300;font-size:32px;color:var(--orange)}
.meta{position:absolute;right:40px;top:48px;font-size:11px;color:var(--muted)}
.meta b{color:var(--orange);font-weight:400}
.title-rule{border-top:1px solid #ddd;margin:14px 0 20px}
.card p{font-size:11px;line-height:14px;margin-bottom:8px}
.photo{width:560px;height:380px;margin:14px auto 26px;background:linear-gradient(160deg,#f2f2f0,#b9b9b4);border:1px solid #ccc}
.card h2{font-family:"Open Sans",sans-serif;font-weight:400;font-size:20px;color:#222;margin:16px 0 12px}
.card h2.big{font-size:26px;margin-top:30px}
.card h3{font-size:12px;font-weight:700;color:#222;margin:14px 0 5px}
.card ul{font-size:11px;line-height:14px;margin:0 0 8px 20px}
a.mail{color:var(--orange);text-decoration:none}
.footer{position:absolute;left:0;top:3100px;width:1200px;height:124px;background:var(--ink)}
.icons{position:absolute;left:400px;top:50px;display:flex;gap:10px}
.icons i{width:24px;height:24px;border:1px solid #666;border-radius:3px}
.copy{position:absolute;right:40px;top:56px;font-size:11px;color:#888}
</style>
</head>
<body>
<aside class="sidebar">
  <div class="side-tab">The Brickleaf Studio</div>
  <div class="search"><span>search</span><i></i></div>
  <p class="intro">Getting an architectural model produced can be expensive and time consuming, but it can also add a lot of value to a project. A scale model lets everyone involved get a very clear understanding of your building.</p>
  <div class="promo one" role="img" aria-label="Promotional banner"></div>
  <div class="promo two" role="img" aria-label="Promotional banner"></div>
  <div class="side-h" style="top:1130px">Newsletter</div>
  <div class="side-rule" style="top:1168px"></div>
  <div class="field" style="top:1182px">Your Name</div>
  <div class="field" style="top:1222px">Email</div>
  <div class="subscribe">Subscribe</div>
  <div class="side-h" style="top:1370px">Contact</div>
  <div class="side-rule" style="top:1408px"></div>
  <div class="map" role="img" aria-label="Map of the studio location"></div>
  <div class="address">14 Larchmont Lane<br>Kestrel Bay NSW<br>2099 Australia<br><br>Phone: +61 2 5550 0142<br>Fax: +61 2 5550 0143<br>Email: <b>info@thebrickleafstudio.example.au</b><br>Website: <b>www.thebrickleafstudio.example.au</b></div>
</aside>

<header class="masthead">
  <div class="brand">
    <div class="brand-mark"></div>
    <div><div class="brand-name">The Brickleaf Studio</div><div class="brand-tag">Architectural Scale Models</div></div>
  </div>
  <nav class="nav">
    <a>Home</a><a>Gallery</a><a>Order Online</a><a>Get a Quote</a><a>Contact</a><a>3D Visualisation</a><a class="active">About Us</a><a>Sitemap</a>
  </nav>
</header>

<main class="card">
  <h1 class="page-title">About Us</h1>
  <div class="meta">Added <b>Nov 20, 2011</b> By <b>Admin</b></div>
  <div class="title-rule"></div>
  <p>If a picture tells a thousand words, a model tells all. We are here to help you get the full story about your project by providing a cost effective and easy way to get a scale model produced and delivered. We are currently serving customers Australia wide and we welcome your enquiry.</p>
  <div class="photo" role="img" aria-label="Photograph of a white architectural scale model"></div>

  <h2>Privacy Statement</h2>
  <h3>Introduction</h3>
  <p>The Brickleaf Studio regards customer privacy as an important part of our relationship with our customers. The following privacy policy applies to all The Brickleaf Studio shops, and conforms to Internet privacy standards. If you have questions or concerns regarding this statement, you should first contact our office manager at <a class="mail">admin@thebrickleafstudio.example.au</a>.</p>
  <h3>Collection of Information</h3>
  <p>In order to use the The Brickleaf Studio website, we may require information from you in order to provide the best service possible. All correspondence may also be collected and stored, particularly in regards to sales, support and accounts, including Email. Any information collected by The Brickleaf Studio is collected via correspondence from you or your company. This may be via the telephone, Email, mail, fax or directly through our website.</p>
  <h3>Use of Collection Information</h3>
  <p>Any details collected from The Brickleaf Studio customers is required in order to provide you with our products and/or services, and a high level of customer service. Correspondence is recorded in order to provide service references, and to assist in our staff development.</p>
  <h3>Storage of Collected Information</h3>
  <p>The security of your personal information is important to us. When you enter sensitive information (such as credit card numbers) on our website, we encrypt that information using secure socket layer technology (SSL). When credit card details are collected, we simply pass them on in order to be processed as required. We never permanently store complete credit card details.</p>
  <p>We follow generally accepted industry standards to protect the personal information submitted to us, both during transmission and once we receive it.</p>
  <p>If you have any questions about security on our website, you can email us at <a class="mail">admin@thebrickleafstudio.example.au</a>.</p>
  <h3>Access of Collection Information</h3>
  <p>If your personally identifiable information changes, or if you no longer desire our service, you may correct, update, delete or deactivate it by emailing us at <a class="mail">admin@thebrickleafstudio.example.au</a>.</p>
  <h3>Orders</h3>
  <p>If you purchase a product or service from us, we may request certain personally identifiable information from you. You may be required to provide contact information (such as name, Email, and postal address) and financial information (such as credit card number, expiration date).</p>
  <p>We use this information for billing purposes and to fill your orders. If we have trouble processing an order, we will use this information to contact you.</p>
  <h3>Communications</h3>
  <p>The Brickleaf Studio uses personally identifiable information for essential communications, such as Emails, accounts information, and critical service details. We may also use this information for other purposes, including some promotional Emails. If at any time a customer wishes not to receive such correspondence, they can request to be removed from any mailing lists by emailing us at <a class="mail">admin@thebrickleafstudio.example.au</a>.</p>
  <p>You will be notified when your personal information is collected by any third party that is not our agent/service provider, so you can make an informed choice as to whether or not to share your information with that party.</p>
  <h3>Third Parties</h3>
  <p>The Brickleaf Studio may at its discretion use other third parties to provide essential services on our site or for our business processes. We may share your details as necessary for the third party to provide that service.</p>
  <p>These third parties are prohibited from using your personally identifiable information for any other purpose. The Brickleaf Studio does not share any information with third parties for any unknown or unrelated uses.</p>
  <h3>Legal</h3>
  <p>We reserve the right to disclose your personally identifiable information as required by law and when we believe that disclosure is necessary to protect our rights and/or comply with a judicial proceeding, court order, or legal process served on our Website.</p>
  <h3>Links</h3>
  <p>Links on the The Brickleaf Studio site to external entities are not covered within this policy. The terms and conditions set out in this privacy statement only cover the domain name of www.thebrickleafstudio.example.au.</p>
  <h3>Changes to Privacy Policy</h3>
  <p>If we decide to change our privacy policy, we will post those changes to this privacy statement, the homepage, and other places we deem appropriate so that you are aware of what information we collect, how we use it, and under what circumstances, if any, we disclose it. We reserve the right to modify this privacy statement at any time, so please review it frequently. If we make material changes to this policy, we will notify you here, by Email, or by means of a notice on our homepage.</p>
  <h3>The Brickleaf Studio Security Policy</h3>
  <p>The Brickleaf Studio uses the PayRiver Payment Gateway for its online credit card transactions. PayRiver processes online credit card transactions for thousands of Australian merchants, providing a safe and secure means of collecting payments via the Internet.</p>
  <p>All online credit card transactions performed on this site using the PayRiver gateway are secured payments.</p>
  <ul>
    <li>Payments are fully automated with an immediate response.</li>
    <li>Your complete credit card number cannot be viewed by The Brickleaf Studio or any outside party.</li>
    <li>All transactions are performed under 128 Bit SSL Certificate.</li>
    <li>All transaction data is encrypted for storage within the PayRiver bank-grade data centre, further protecting your credit card data.</li>
    <li>PayRiver is an authorised third party processor for all the major Australian banks.</li>
    <li>PayRiver at no time touches your funds; all monies are directly transferred from your credit card to the merchant account held by The Brickleaf Studio.</li>
  </ul>
  <p>For more information about PayRiver and online credit card payments, please visit our payment partner's website.</p>

  <h2 class="big">Delivery Policy</h2>
  <h3>Physical Goods</h3>
  <p>After ordering online, you will receive an email confirmation from PayRiver containing your order details (if you have provided your email address). We will normally confirm receipt of your order within a few minutes of ordering. We will attempt to send your goods via hand delivery on the nominated date, however if goods are unavailable delivery will take a little longer. If you wish to query a delivery please contact us at <a class="mail">admin@thebrickleafstudio.example.au</a>.</p>
  <h3>Digital Delivery</h3>
  <p>After ordering online, you will receive an email confirmation from PayRiver containing your order details (if you have provided your email address). We will normally confirm receipt of your order within a few minutes of ordering. If you wish to query a delivery please contact us at <a class="mail">admin@thebrickleafstudio.example.au</a>.</p>
  <h3>Refund &amp; Returns Policy</h3>
  <p>If you are not completely satisfied with your purchase we will give you a 14 day money-back guarantee from the time you receive the goods. Please email us at <a class="mail">admin@thebrickleafstudio.example.au</a> within that time if you are not satisfied with your purchase so that we can resolve any problems.</p>
  <p>This refund policy does not apply to goods which have been worn or used, damaged after delivery, or if any attempt has been made to alter the product or if they have been dropped or broken. All products must be returned in their original condition, all postage and insurance costs are to be paid by the buyer. We recommend that you return the product via Registered post and that you pay for all postage. We assume no responsibility for goods lost or damaged in transit and therefore advise you take a consignment registration of insurance with your postal carrier. The Brickleaf Studio will not be responsible for parcels lost or damaged in transit if you choose not to insure.</p>
</main>

<footer class="footer">
  <div class="icons"><i></i><i></i><i></i><i></i><i></i></div>
  <div class="copy">2011 © Copyright The Brickleaf Studio · Site map · Phone: +61 2 5550 0142 · Australia</div>
</footer>
</body>
</html>
```